A new presentation to our clients

we are a Real Estate agency, our website is www.lumibrasa.com and it’s time to have a new, fashion and remarcable Business Card. we want to differentiate ourselves from other companies so we want a business card that differentiates us. we want the business card to impact our customers. in the competitive market that we have today, we have to be different and it is this difference that we seek

Target Market(s)

Real Estate Clients

Contact Information for Business Card

We search a totaly diferent card from the usual

Font styles to use
Sans Serif

Colors
e34197

Requirements
Must have
• Logo, adress, phone contact, e-mail, photo, and our website
Nice to have
• We would like to see a modern business card
Should not have
• Houses or building draws

```html
<!DOCTYPE html>
<html lang="en">
<head>
<meta charset="utf-8">
<title>Lumibrasa Business Card</title>
<link rel="stylesheet" href="https://fonts.googleapis.com/css2?family=Montserrat:wght@500;600;700&display=swap">
<style>
  :root {
    --brand-pink: #e3226f;
    --ink-grey: #7d7d7d;
    --text-grey: #6a6a6a;
    --card-white: #ffffff;
    --backdrop: #2a2a2a;
    --divider: #c9c9c9;
  }
  * { margin: 0; padding: 0; box-sizing: border-box; }
  html, body {
    width: 1200px;
    height: 791px;
    overflow: hidden;
    background: var(--backdrop);
    font-family: "Montserrat", sans-serif;
  }
  .card {
    position: absolute;
    left: 100px;
    top: 110px;
    width: 1000px;
    height: 570px;
    background: var(--card-white);
    border-radius: 26px;
    overflow: hidden;
  }
  .card__band {
    position: absolute;
    left: 0;
    bottom: 0;
    width: 100%;
    height: 19px;
    background: var(--brand-pink);
  }
  .brand-name {
    position: absolute;
    left: 98px;
    top: 236px;
    font-size: 70px;
    font-weight: 600;
    line-height: 1;
    color: var(--brand-pink);
    letter-spacing: 0.5px;
  }
  .divider {
    position: absolute;
    left: 538px;
    top: 151px;
    width: 2px;
    height: 275px;
    background: linear-gradient(to bottom, transparent, var(--divider) 20%, var(--divider) 80%, transparent);
  }
  .contact {
    position: absolute;
    left: 581px;
    top: 155px;
    color: var(--text-grey);
  }
  .contact__name {
    font-size: 33px;
    font-weight: 700;
    color: var(--brand-pink);
    line-height: 1;
    letter-spacing: 0.3px;
  }
  .contact__role {
    margin-top: 8px;
    font-size: 24px;
    font-weight: 600;
    color: var(--ink-grey);
    line-height: 1;
    letter-spacing: 0.5px;
  }
  .contact__address {
    margin-top: 24px;
    font-size: 21px;
    font-weight: 500;
    line-height: 27px;
  }
  .contact__list {
    list-style: none;
    margin-top: 18px;
  }
  .contact__item {
    display: flex;
    align-items: center;
    height: 29px;
    font-size: 21px;
    font-weight: 500;
  }
  .contact__icon {
    width: 20px;
    height: 20px;
    margin-right: 18px;
    fill: var(--brand-pink);
    flex: none;
  }
</style>
</head>
<body>
  <main class="card">
    <div class="brand-name">Lumibrasa</div>
    <div class="divider"></div>
    <section class="contact">
      <h1 class="contact__name">RITA ALMEIDA</h1>
      <p class="contact__role">CEO/FOUNDER</p>
      <p class="contact__address">Rua das Camélias, 148<br>4050-265, Porto Norte</p>
      <ul class="contact__list">
        <li class="contact__item">
          <svg class="contact__icon" viewBox="0 0 20 20" aria-hidden="true"><path d="M4 1.5l3.2 3.6-1.6 2.4c1 2.3 2.7 4 5 5l2.4-1.6 3.6 3.2-1.6 3C9 17 3 11 1.9 3.2z"/></svg>
          (+351) 220 481 356
        </li>
        <li class="contact__item">
          <svg class="contact__icon" viewBox="0 0 20 20" aria-hidden="true"><path d="M5 1h10v5H5z"/><path d="M1 7h18v8h-3v-3H4v3H1z"/><path d="M5 13h10v6H5z"/></svg>
          (+351) 220 481 357
        </li>
        <li class="contact__item">
          <svg class="contact__icon" viewBox="0 0 20 20" aria-hidden="true"><path d="M1 4h18v1.5l-9 6-9-6z"/><path d="M1 7.5l9 6 9-6V16H1z"/></svg>
          geral@lumibrasa.com
        </li>
        <li class="contact__item">
          <svg class="contact__icon" viewBox="0 0 20 20" aria-hidden="true"><circle cx="10" cy="10" r="9"/></svg>
          www.lumibrasa.com
        </li>
      </ul>
    </section>
    <div class="card__band"></div>
  </main>
</body>
</html>
```